Corporate Business Card

Very professional, Modern, Not to busy, include phone address email, website
(253) 617-4930, 18761 52nd Avenue S, Kent, WA 98047, martin@plumlinegroup.com, varkoworks.com

Target Market(s)

Manufacturing

Industry/Entity Type

Aero, machining, manufacturing, Off road racing

Contact Information for Business Card

Phone, address email, website

```html
<!DOCTYPE html>
<html lang="en">
<head>
<meta charset="utf-8">
<title>Varko Works – Business Card</title>
<link rel="stylesheet" href="https://fonts.googleapis.com/css2?family=Open+Sans:wght@400&family=Roboto:wght@500;700&family=Roboto+Mono:wght@400&display=swap">
<style>
  :root {
    --page: #d3d3d3;
    --card-dark: #0e0e0e;
    --card-sheen: #5a5a5a;
    --red: #b5140e;
    --red-bright: #f20c06;
    --red-deep: #7a0302;
    --navy: #15356e;
    --white: #ffffff;
    --gear-grey: #4a4a4a;
  }
  * { margin: 0; padding: 0; box-sizing: border-box; }
  html, body {
    width: 960px; height: 1200px; overflow: hidden;
    background: var(--page);
  }
  .card {
    position: absolute; left: 12px; width: 935px; height: 550px;
    overflow: hidden; background: var(--card-dark);
  }
  .card--front {
    top: 27px;
    background:
      radial-gradient(ellipse 300px 160px at 300px 110px, rgba(110,110,110,.55), transparent 70%),
      radial-gradient(ellipse 500px 120px at 640px 500px, rgba(120,120,120,.45), transparent 75%),
      var(--card-dark);
  }
  .card--back {
    top: 612px;
    background:
      radial-gradient(ellipse 360px 130px at 200px 90px, rgba(120,120,120,.5), transparent 70%),
      radial-gradient(ellipse 460px 110px at 500px 500px, rgba(120,120,120,.45), transparent 75%),
      linear-gradient(180deg, #2a2a2a, #121212 60%, #222);
  }
  .card__shapes { position: absolute; inset: 0; width: 935px; height: 550px; }

  .holder { position: absolute; left: 56px; top: 68px; color: var(--white); }
  .holder__name {
    font-family: "Roboto", sans-serif; font-weight: 500;
    font-size: 48px; letter-spacing: 2px; line-height: 1;
  }
  .holder__role {
    margin-top: 16px;
    font-family: "Roboto Mono", monospace; font-size: 24px;
    letter-spacing: 14px; line-height: 1;
  }
  .holder__rule {
    position: absolute; left: 56px; top: 174px; width: 310px; height: 2px;
    background: var(--white);
  }
  .holder__rule::before {
    content: ""; position: absolute; left: 0; top: -2px;
    width: 86px; height: 6px; border-radius: 3px; background: var(--navy);
  }

  .contact { position: absolute; display: flex; align-items: center; gap: 18px;
    font-family: "Open Sans", sans-serif; font-size: 23px; color: var(--white); }
  .contact__icon {
    width: 40px; height: 40px; background: var(--white);
    display: flex; align-items: center; justify-content: center; flex: none;
  }
  .contact__icon svg { width: 28px; height: 28px; }
  .contact--phone { left: 570px; top: 129px; }
  .contact--email { left: 498px; top: 214px; }
  .contact--address { left: 428px; top: 298px; font-size: 22px; }
  .contact--web { left: 366px; top: 383px; }

  .dot-field {
    position: absolute; left: 861px; top: 378px; width: 70px; height: 80px;
    background: rgba(60,0,0,.25);
  }
  .gear-art {
    position: absolute;
    background: radial-gradient(closest-side, rgba(80,80,80,.75), rgba(74,74,74,.25) 80%, transparent);
  }
  .gear-art--front { left: 0; top: 429px; width: 170px; height: 121px; }
  .gear-art--back { left: 664px; top: 16px; width: 271px; height: 221px; }

  .brand {
    position: absolute; left: 0; right: 0; top: 215px; text-align: center;
    font-family: "Roboto", sans-serif; font-weight: 700; font-size: 72px;
    letter-spacing: 4px; color: var(--navy); line-height: 1;
  }
</style>
</head>
<body>

<section class="card card--front">
  <svg class="card__shapes" viewBox="0 0 935 550" aria-hidden="true">
    <polygon fill="var(--navy)" points="0,317 400,317 400,400 0,400"/>
    <polygon fill="var(--red-deep)" points="159,400 291,400 224,479"/>
    <polygon fill="var(--red)" points="563,72 935,72 935,479 224,479"/>
  </svg>

  <div class="holder">
    <h1 class="holder__name">MARTIN</h1>
    <p class="holder__role">POSITION</p>
  </div>
  <div class="holder__rule"></div>

  <div class="contact contact--phone">
    <span class="contact__icon"><svg viewBox="0 0 24 24"><path fill="var(--red)" d="M6.6 3.5l2.6 3.4-1.7 2.1c1 2.2 2.8 4 5 5l2.1-1.7 3.4 2.6-1.3 3c-6.5.4-12.3-5.4-11.9-11.9z"/><path d="M14 4.5a6 6 0 0 1 5.5 5.5M14 7.5a3 3 0 0 1 2.5 2.5" stroke="var(--red)" stroke-width="1.6" fill="none"/></svg></span>
    <span>(253) 617-4930</span>
  </div>
  <div class="contact contact--email">
    <span class="contact__icon"><svg viewBox="0 0 24 24"><rect x="2.5" y="5.5" width="19" height="13" fill="none" stroke="var(--red)" stroke-width="1.6"/><path d="M2.5 5.5l9.5 8 9.5-8M2.5 18.5l7-6.5M21.5 18.5l-7-6.5" fill="none" stroke="var(--red)" stroke-width="1.6"/></svg></span>
    <span>martin@plumlinegroup.com</span>
  </div>
  <div class="contact contact--address">
    <span class="contact__icon"><svg viewBox="0 0 24 24"><path fill="var(--red)" d="M12 2a7 7 0 0 0-7 7c0 5 7 13 7 13s7-8 7-13a7 7 0 0 0-7-7zm0 9.5a2.5 2.5 0 1 1 0-5 2.5 2.5 0 0 1 0 5z"/></svg></span>
    <span>18761 52nd Avenue S, Kent, WA 98047</span>
  </div>
  <div class="contact contact--web">
    <span class="contact__icon"><svg viewBox="0 0 24 24" fill="none" stroke="var(--red)" stroke-width="1.3"><circle cx="12" cy="12" r="9"/><ellipse cx="12" cy="12" rx="4" ry="9"/><path d="M3 12h18M4.5 7.5h15M4.5 16.5h15M12 3v18"/></svg></span>
    <span>varkoworks.com</span>
  </div>

  <div class="dot-field" role="img" aria-label="Dot grid decoration"></div>
  <div class="gear-art gear-art--front" role="img" aria-label="Grey gear decoration"></div>
</section>

<section class="card card--back">
  <svg class="card__shapes" viewBox="0 0 935 550" aria-hidden="true">
    <defs>
      <linearGradient id="red-fade" x1="0" y1="0" x2="0" y2="1">
        <stop offset="0" stop-color="var(--red-deep)"/>
        <stop offset="1" stop-color="var(--red-bright)"/>
      </linearGradient>
      <linearGradient id="fold-fade" x1="0" y1="0" x2="1" y2="0">
        <stop offset="0" stop-color="#3a0000"/>
        <stop offset="1" stop-color="var(--red)"/>
      </linearGradient>
    </defs>
    <polygon fill="url(#red-fade)" points="0,248 226,472 0,472"/>
    <polygon fill="url(#red-fade)" points="935,248 935,472 709,472"/>
    <polygon fill="url(#fold-fade)" points="161,407 291,407 226,472"/>
    <polygon fill="url(#fold-fade)" points="643,407 772,407 708,472"/>
    <polygon fill="var(--navy)" points="107,353 825,353 771,407 161,407"/>
  </svg>

  <div class="gear-art gear-art--back" role="img" aria-label="Grey gear cluster decoration"></div>
  <p class="brand">VARKO WORKS</p>
</section>

</body>
</html>
```